Stationery Design Project

We need a stationery design for our Norwegian trucking company. We have existed for about 15 years and our 12 drivers uses relatively new vehicles to transport goods around in northern Norway. Long distance routes with fresh fish og food transport is our main operations.

We have already made alogo that's printed on our trucks. The logo and a picture of our trucks is attached. I think the logo i crappy, but since its already in use, changing it is not an option in this round. Still using a better colour scheme in the overall stationery and more interesting fonts is possible (altso in the logo).

Company details:
Name: Kjelvraket AS
Organisation nr 873 615 309
Post adress: 8642 Raudvik

I like minimalism and simplicity. I am avalibly for questions in normal GMT working hours either here or on mail: ivar@fjordlast.no

Reason: Hi. Im extending the deadline because I needed some time to find a vector file of our logo. Sorry for the inconvenience

Hi, and thanks for all your interest in the project. Some updates:

-          I have decided to commit to using one of the designs. Some designer will get the payment.

-          I have extended the deadline with 24 hours since I needed some time to find our firms vector logo (a slow Swedish man was holding me up)

-          We will not choose a design before the deadline. No need to rush.

-          We have received a lot of great design and think there is a need to specified the product we want to make:

o   Business Card for all our employers. I just need the design and will duplicate with the correct numbers and name myself. The information on should be: Logo, employer’s name, Phone number, email, website, Postal number and address. Use this as a template: logo, Leif Brattvoll, 47382066, Leif@fjordlast.no,, fjordlast.no, 8642 Raudvik. The order and placement of the information is your creative decision.

o   Stickers to put on the goods we travel. On the sticker the should be the following information: Logo, phone number, Tekst and link: Fraktæ av Kjelvraket. Ke du syns? Fjordlast.no/tilbakemelding (this means: Handled by Kjelvraket. What do you think Fjordlast.no/feedback -à the link will be a feedback form). The placement the information and size is your creative decision with some stings: we have been thinking of using Drukko for printing and see that a size about 6x6 cm, 8x5 or something like that. (with 3000 copies our budget is 200 punds). Any suggestions of other suppliers are welcome. Drukko price calculator http://www.drukkolabelhouse.co.uk/digital-litho-printing/printing-labels-tags/stickers/

o   Letterhead with logo, address, phone number and organizational number.

o   Envelopes with logo,address, phone number and organizational number.

Have a nice day.

 

 

• Using the blue colour in the logo and using a similar graphic approch.

```html
<!DOCTYPE html>
<html lang="no">
<head>
<meta charset="utf-8">
<title>Kjelvraket – visittkort</title>
<link rel="stylesheet" href="https://fonts.googleapis.com/css2?family=Open+Sans:wght@400;600;700;800&display=swap">
<style>
  :root {
    --stage: #8a8d92;
    --paper: #ffffff;
    --blue-deep: #0b4c9e;
    --blue-bright: #0a72b8;
    --ink: #1b2233;
    --rule: #c9ccd2;
  }
  * { box-sizing: border-box; margin: 0; padding: 0; }
  html, body { width: 1200px; height: 751px; overflow: hidden; }
  body {
    position: relative;
    background: var(--stage);
    font-family: "Open Sans", Arial, sans-serif;
  }
  .card {
    position: absolute;
    width: 525px;
    height: 300px;
    overflow: hidden;
  }
  .card--front { left: 55px; top: 52px; background: var(--paper); }
  .card--white { left: 621px; top: 55px; background: var(--paper); border: 1px solid var(--rule); }
  .card--deep { left: 55px; top: 395px; background: var(--blue-deep); }
  .card--bright { left: 621px; top: 395px; background: var(--blue-bright); }

  .card__swoosh { position: absolute; inset: 0; }

  .wordmark {
    font-weight: 800;
    letter-spacing: -0.5px;
    line-height: 1;
    white-space: nowrap;
  }
  .card--front .wordmark {
    position: absolute; left: 30px; top: 78px;
    font-size: 44px; color: var(--blue-deep);
  }
  .card--white .wordmark,
  .card--deep .wordmark,
  .card--bright .wordmark {
    position: absolute; left: 0; right: 0; top: 122px;
    text-align: center; font-size: 54px;
  }
  .card--white .wordmark { color: var(--blue-deep); }
  .card--deep .wordmark, .card--bright .wordmark { color: var(--paper); }

  .website {
    position: absolute; left: 0; right: 0; top: 248px;
    text-align: center; font-size: 17px; letter-spacing: 3.4px;
  }
  .card--white .website { color: var(--ink); }
  .card--deep .website, .card--bright .website { color: var(--paper); }

  .contact {
    position: absolute; left: 29px; top: 166px;
    list-style: none; font-size: 14px; color: var(--ink); line-height: 19px;
  }
  .contact li { display: flex; align-items: center; gap: 5px; }
  .contact .contact__org { color: var(--blue-bright); }
  .contact .contact__post { margin-top: 19px; }
  .contact svg { width: 11px; height: 11px; fill: var(--blue-deep); flex: none; }

  .holder {
    position: absolute; right: 19px; bottom: 19px;
    font-size: 18px; font-weight: 700; color: var(--paper);
  }
</style>
</head>
<body>

  <section class="card card--front" aria-label="Visittkort, forside">
    <svg class="card__swoosh" viewBox="0 0 525 300" aria-hidden="true">
      <path d="M245,300 C350,258 392,150 282,0 L525,0 L525,300 Z" fill="var(--blue-deep)"/>
      <path d="M268,300 C385,240 405,128 352,0 L372,0 C428,120 402,240 292,300 Z" fill="var(--paper)"/>
      <path d="M298,292 C420,222 468,118 478,0 L505,0 C500,130 432,232 298,292 Z" fill="var(--blue-bright)"/>
      <path d="M305,290 C440,236 500,140 510,0 L517,0 C512,146 450,240 305,290 Z" fill="var(--paper)"/>
    </svg>
    <div class="wordmark">Kjelvraket</div>
    <ul class="contact">
      <li><svg viewBox="0 0 12 12"><path d="M2.5 0.5l2 2.5-1.2 1.4a7 7 0 0 0 4.3 4.3l1.4-1.2 2.5 2-1.3 2C5.5 11.5 0.5 6.5 0.5 1.8z"/></svg>47382066</li>
      <li class="contact__org">Org nr <span style="color:var(--ink)">873 615 309</span></li>
      <li><svg viewBox="0 0 12 12"><path d="M0.5 2.5h11v7h-11z M1 3l5 3.6 5-3.6" /></svg>Leif@fjordlast.no</li>
      <li><svg viewBox="0 0 12 12"><circle cx="6" cy="6" r="5.5"/></svg>www.fjordlast.no</li>
      <li class="contact__post"><svg viewBox="0 0 12 12"><path d="M1 11V4l5-3 5 3v7h-3.5V7.5h-3V11z"/></svg>8642 Raudvik</li>
    </ul>
    <div class="holder">Leif Brattvoll</div>
  </section>

  <section class="card card--white" aria-label="Visittkort, bakside hvit">
    <div class="wordmark">Kjelvraket</div>
    <div class="website">www.fjordlast.no</div>
  </section>

  <section class="card card--deep" aria-label="Visittkort, bakside mørkeblå">
    <div class="wordmark">Kjelvraket</div>
    <div class="website">www.fjordlast.no</div>
  </section>

  <section class="card card--bright" aria-label="Visittkort, bakside lyseblå">
    <div class="wordmark">Kjelvraket</div>
    <div class="website">www.fjordlast.no</div>
  </section>

</body>
</html>
```